One of a kind service business!

We are the only ocean freight auditing company in the entire world that does what we do. We provide a innovative service in auditing our clients invoices for billing errors as it relates to the import and export of their products anywhere in the world. We'd like to retain the current logo - but we are open to any interesting concepts that can complete the card.

Target Market(s)

C-Level and Senior Financial executives

Industry/Entity Type

Auditing

Requirements
Must have

• ONE SIDED ONLY
Should not have
• no cartoonish images

```html
<!DOCTYPE html>
<html lang="en">
<head>
<meta charset="utf-8">
<title>Harborline Audit – Business Card</title>
<link rel="stylesheet" href="https://fonts.googleapis.com/css2?family=Ubuntu:wght@500;700&family=Open+Sans:wght@400;700&display=swap">
<style>
  :root {
    --bg: #eef1f4;
    --card: #ffffff;
    --blue: #1592cf;
    --blue-deep: #1b84bf;
    --navy: #1b2a57;
    --grey: #a7a9ac;
    --ink: #1a1a1a;
    --icon-fill: #2a9ad6;
  }
  * { margin: 0; padding: 0; box-sizing: border-box; }
  html, body { width: 975px; height: 1200px; overflow: hidden; background: var(--bg); }
  .sheet { position: relative; width: 975px; height: 1200px; }
  .card {
    position: absolute; left: 93px; width: 793px; height: 454px;
    background: var(--card); border-radius: 24px; overflow: hidden;
    box-shadow: 0 4px 14px rgba(0,0,0,0.18);
  }
  .card--front { top: 89px; }
  .card--back { top: 643px; }
  .card__waves { position: absolute; left: 0; top: 0; width: 793px; height: 454px; }
  .brand {
    position: absolute; left: 0; right: 0; display: flex; justify-content: center; align-items: center; gap: 14px;
    font-family: "Ubuntu", sans-serif; font-weight: 700; font-size: 50px; color: var(--blue); letter-spacing: 1px;
  }
  .brand__mark { width: 22px; height: 22px; background: var(--navy); }
  .card--front .brand { top: 90px; }
  .card--back .brand { top: 66px; }
  .holder {
    position: absolute; left: 100px; top: 224px;
    font-family: "Ubuntu", sans-serif; font-weight: 500; font-size: 31px; color: var(--blue-deep); letter-spacing: 0.5px;
  }
  .contact {
    position: absolute; display: flex; align-items: center; gap: 9px;
    font-family: "Open Sans", sans-serif; font-size: 19px; color: var(--ink);
  }
  .contact svg { width: 22px; height: 22px; flex: none; }
  .contact--phone { left: 95px; top: 279px; font-size: 20px; }
  .contact--phone svg { width: 28px; height: 28px; }
  .contact--web { left: 452px; top: 236px; }
  .contact--mail { left: 452px; top: 268px; }
  .pitch { position: absolute; left: 0; right: 0; text-align: center; font-family: "Open Sans", sans-serif; color: var(--ink); }
  .pitch__title { top: 184px; font-size: 22px; font-weight: 700; }
  .pitch__body { top: 232px; font-size: 21px; line-height: 31px; }
  .pitch__body strong { font-weight: 700; }
  .contact--footer { left: 508px; top: 408px; color: #ffffff; font-size: 19px; }
</style>
</head>
<body>
<main class="sheet">

  <section class="card card--front">
    <svg class="card__waves" viewBox="0 0 793 454" aria-hidden="true">
      <path fill="var(--grey)" d="M0,330 C150,395 320,402 460,374 C540,358 590,352 625,352 C560,360 500,372 450,386 C310,425 140,415 0,352 Z"/>
      <path fill="var(--blue)" d="M0,364 C150,430 300,440 430,410 C560,380 680,362 793,410 L793,454 L0,454 Z"/>
    </svg>
    <div class="brand"><span class="brand__name">Harborline Audit</span><span class="brand__mark"></span></div>
    <h1 class="holder">Daniel Moreau</h1>
    <div class="contact contact--phone">
      <svg viewBox="0 0 28 28" aria-hidden="true"><circle cx="14" cy="14" r="14" fill="#c9e3f3"/><rect x="9" y="6" width="10" height="16" rx="2" fill="var(--icon-fill)"/><rect x="11" y="8" width="6" height="6" fill="#ffffff"/></svg>
      <span>1-555-014-2368</span>
    </div>
    <div class="contact contact--web">
      <svg viewBox="0 0 22 22" aria-hidden="true"><circle cx="11" cy="11" r="11" fill="var(--icon-fill)"/><g fill="none" stroke="#ffffff" stroke-width="1.3"><circle cx="11" cy="11" r="6"/><ellipse cx="11" cy="11" rx="2.6" ry="6"/><path d="M5 11h12"/></g></svg>
      <span>www.harborlineaudit.net</span>
    </div>
    <div class="contact contact--mail">
      <svg viewBox="0 0 22 22" aria-hidden="true"><circle cx="11" cy="11" r="11" fill="var(--icon-fill)"/><text x="11" y="15.5" text-anchor="middle" font-family="Open Sans, sans-serif" font-size="13" font-weight="700" fill="#ffffff">@</text></svg>
      <span>danielm@harborlineaudit.net</span>
    </div>
  </section>

  <section class="card card--back">
    <svg class="card__waves" viewBox="0 0 793 454" aria-hidden="true">
      <path fill="var(--grey)" d="M0,330 C150,395 320,402 460,374 C540,358 590,352 625,352 C560,360 500,372 450,386 C310,425 140,415 0,352 Z"/>
      <path fill="var(--blue)" d="M0,364 C150,430 300,440 430,410 C560,380 680,362 793,410 L793,454 L0,454 Z"/>
    </svg>
    <div class="brand"><span class="brand__name">Harborline Audit</span><span class="brand__mark"></span></div>
    <h2 class="pitch pitch__title">HUGE REFUNDS ON OCEAN FREIGHT INVOICES!</h2>
    <p class="pitch pitch__body">Over 10% of container shipping industry invoices<br>are inaccurate - so talk to <strong>HARBORLINE AUDIT</strong> today about<br>securing your OCEAN FREIGHT REFUNDS....</p>
    <div class="contact contact--footer">
      <svg viewBox="0 0 22 22" aria-hidden="true"><circle cx="11" cy="11" r="11" fill="#ffffff"/><g fill="none" stroke="var(--blue)" stroke-width="1.3"><circle cx="11" cy="11" r="6"/><ellipse cx="11" cy="11" rx="2.6" ry="6"/><path d="M5 11h12"/></g></svg>
      <span>www.harborlineaudit.net</span>
    </div>
  </section>

</main>
</body>
</html>
```